design a catchy flyer for my electrical buisness

need a flyer designed to attract people to my business by looking professional and offering specials

Target Market(s)

all people i want to look affordable to everyone but still keeping that professional look and feel

Industry/Entity Type

Electrical

Requirements
Must have
• NO JOB TO BIG OR SMALL
• CALL NOW FOR A FREE QUOTE 0400817326
• NO CALL OUT FEE
• same promises as uploaded pic maybe written different style
• Your neighborhood electrician
• 100% satisfaction guaranteed
• were here to help
• mention this flyer for 10% off
• specializing in house renovations, extensions, kitchen and bathroom upgrades switchboard upgrades
• Make your house safe with our RCD and smoke alarm packages
Nice to have
• modern
• proffesional
• shows trust when customers read it
Should not have
• corny slogans
• cheap look

```html
<!DOCTYPE html>
<html lang="en">
<head>
<meta charset="utf-8">
<title>Neighborhood Electrician Flyer</title>
<link rel="stylesheet" href="https://fonts.googleapis.com/css2?family=Roboto+Condensed:wght@300;400;700;900&display=swap">
<style>
:root{
  --navy:#1d2f8c;
  --blue:#0a5fc4;
  --sky:#1aa3e6;
  --yellow:#ffd400;
  --gold:#ffcc00;
  --red:#d8141f;
  --deep-red:#b5121b;
  --white:#ffffff;
  --ink:#1a1a1a;
  --tick:#1c8fe0;
  --orange:#f07a1a;
  --stage:#1d2431;
}
*{margin:0;padding:0;box-sizing:border-box}
html,body{width:1200px;height:1200px;overflow:hidden;background:var(--stage)}
body{font-family:"Roboto Condensed",Arial,sans-serif}
.flyer{position:absolute;left:185px;top:20px;width:830px;height:1160px;overflow:hidden;
  background:linear-gradient(180deg,var(--gold) 0%,var(--yellow) 45%,#fff3b8 80%,var(--white) 92%)}
.flyer-shapes{position:absolute;left:0;top:0}
.photo{position:absolute;left:470px;top:60px;width:360px;height:485px;
  background:linear-gradient(180deg,#5b79d8 0%,#3c55c2 55%,#2f47a8 100%);border-radius:180px 0 0 0}
.tagline{position:absolute;left:110px;top:128px;color:var(--white);font-weight:700;font-size:36px}
.neighborhood{position:absolute;left:44px;top:180px;color:var(--white);font-weight:700;font-size:50px;letter-spacing:.5px}
.headline{position:absolute;left:20px;top:240px;color:var(--yellow);font-weight:900;font-size:112px;letter-spacing:-1px;
  text-shadow:4px 4px 0 var(--navy),-2px -2px 0 var(--navy),2px -2px 0 var(--navy),-2px 2px 0 var(--navy)}
.badge{position:absolute;left:325px;top:385px;width:190px;height:190px}
.badge-text{position:absolute;left:325px;top:428px;width:190px;text-align:center;color:var(--white);font-weight:700;line-height:1}
.badge-text .pct{font-size:54px;font-weight:900;display:block}
.badge-text .sub{font-size:25px;display:block;margin-top:4px}
.section-title{position:absolute;left:34px;top:562px;color:var(--red);font-weight:900;font-size:30px}
.promises{position:absolute;left:30px;top:612px;width:470px;list-style:none;color:var(--ink);font-size:20px;line-height:1.18}
.promises li{position:relative;padding-left:28px;margin-bottom:12px}
.promises svg{position:absolute;left:0;top:3px}
.services{position:absolute;left:500px;top:560px;width:290px;height:455px;background:var(--red)}
.services ul{list-style:none;padding:48px 16px 0 30px;color:var(--white);font-size:20px;line-height:1.2}
.services li{position:relative;margin-bottom:22px}
.services li::before{content:"";position:absolute;left:-16px;top:8px;width:6px;height:6px;border-radius:50%;background:var(--white)}
.services strong{font-weight:700}
.discount{position:absolute;left:485px;top:860px;width:270px;height:170px}
.discount-text{position:absolute;left:485px;top:903px;width:270px;text-align:center;color:var(--white);font-size:62px;font-weight:900}
.discount-text span{font-weight:400}
.cta{position:absolute;left:0;top:1040px;width:830px;text-align:center;font-size:34px;color:var(--ink);font-weight:400}
.cta .accent{color:var(--blue);font-weight:700}
.brand{position:absolute;left:0;top:1100px;width:830px;display:flex;justify-content:center;align-items:center;gap:14px}
.brand-dot{width:40px;height:40px;border-radius:50%;background:var(--orange)}
.brand-name{font-size:34px;font-weight:400;color:var(--orange)}
</style>
</head>
<body>
<main class="flyer">
  <svg class="flyer-shapes" width="830" height="1160" viewBox="0 0 830 1160" aria-hidden="true">
    <defs>
      <linearGradient id="sky" x1="0" y1="0" x2="1" y2="0">
        <stop offset="0" stop-color="#1d2f8c"/>
        <stop offset=".55" stop-color="#0a5fc4"/>
        <stop offset="1" stop-color="#1aa3e6"/>
      </linearGradient>
    </defs>
    <path d="M0,0 H830 V575 L560,575 C380,575 110,500 0,262 Z" fill="#d8141f"/>
    <path d="M0,0 H830 V545 L560,545 C380,545 120,470 0,240 Z" fill="url(#sky)"/>
  </svg>

  <div class="photo" role="img" aria-label="Smiling electrician in blue overalls carrying a coil of cable, with a multimeter and tool belt"></div>

  <p class="tagline">were here to help</p>
  <p class="neighborhood">Your Neighborhood</p>
  <h1 class="headline">Electrician</h1>

  <svg class="badge" viewBox="-95 -95 190 190" aria-hidden="true">
    <polygon fill="#d8141f" points="92,0 78.5,15.6 85,35.2 66.5,44.5 65,65 44.5,66.5 35.2,85 15.6,78.5 0,92 -15.6,78.5 -35.2,85 -44.5,66.5 -65,65 -66.5,44.5 -85,35.2 -78.5,15.6 -92,0 -78.5,-15.6 -85,-35.2 -66.5,-44.5 -65,-65 -44.5,-66.5 -35.2,-85 -15.6,-78.5 0,-92 15.6,-78.5 35.2,-85 44.5,-66.5 65,-65 66.5,-44.5 85,-35.2 78.5,-15.6"/>
  </svg>
  <p class="badge-text"><span class="pct">100%</span><span class="sub">satisfaction</span><span class="sub">guaranteed</span></p>

  <h2 class="section-title">NO JOB TO BIG OR SMALL</h2>
  <ul class="promises">
    <li><svg width="18" height="14" viewBox="0 0 18 14"><path d="M1,7 L6,12 L17,1" fill="none" stroke="#1c8fe0" stroke-width="3.5"/></svg>We will provide you with a fixed price gurantee assuring no extra costs</li>
    <li><svg width="18" height="14" viewBox="0 0 18 14"><path d="M1,7 L6,12 L17,1" fill="none" stroke="#1c8fe0" stroke-width="3.5"/></svg>We will leave your place as clean as when we arrived</li>
    <li><svg width="18" height="14" viewBox="0 0 18 14"><path d="M1,7 L6,12 L17,1" fill="none" stroke="#1c8fe0" stroke-width="3.5"/></svg>We will rovide a 12 Month warranty on all parts</li>
    <li><svg width="18" height="14" viewBox="0 0 18 14"><path d="M1,7 L6,12 L17,1" fill="none" stroke="#1c8fe0" stroke-width="3.5"/></svg>We will provide friendly, helpful service and advice</li>
    <li><svg width="18" height="14" viewBox="0 0 18 14"><path d="M1,7 L6,12 L17,1" fill="none" stroke="#1c8fe0" stroke-width="3.5"/></svg>We will arrive on time or we will pay you $100</li>
    <li><svg width="18" height="14" viewBox="0 0 18 14"><path d="M1,7 L6,12 L17,1" fill="none" stroke="#1c8fe0" stroke-width="3.5"/></svg>Before any job begins you will know the exat cost</li>
    <li><svg width="18" height="14" viewBox="0 0 18 14"><path d="M1,7 L6,12 L17,1" fill="none" stroke="#1c8fe0" stroke-width="3.5"/></svg>If there is a problem and it's our fault we will fix it for free</li>
    <li><svg width="18" height="14" viewBox="0 0 18 14"><path d="M1,7 L6,12 L17,1" fill="none" stroke="#1c8fe0" stroke-width="3.5"/></svg>We will return your telephone calls promptly</li>
    <li><svg width="18" height="14" viewBox="0 0 18 14"><path d="M1,7 L6,12 L17,1" fill="none" stroke="#1c8fe0" stroke-width="3.5"/></svg>No Call Out Fee</li>
  </ul>

  <aside class="services">
    <ul>
      <li>Specializing in house renovations, extensions, kitchen and bathroom upgrades, Switchboard upgrades.</li>
      <li>Make your house safe with our <strong>RCD and smoke alarm packages.</strong></li>
    </ul>
  </aside>
  <svg class="discount" viewBox="0 0 270 170" aria-hidden="true">
    <ellipse cx="135" cy="85" rx="128" ry="76" fill="#d8141f" stroke="#ffffff" stroke-width="5"/>
  </svg>
  <p class="discount-text">10% <span>off</span></p>

  <p class="cta">CALL NOW FOR A <span class="accent">FREE QUOTE &nbsp;- 0400 817 326</span></p>

  <div class="brand">
    <span class="brand-dot"></span>
    <span class="brand-name">VoltBridge</span>
  </div>
</main>
</body>
</html>
```